Bramblewood Card Company Business Cards

We are a trading card store with Glimmorax, sports and other TCG cards, we need a business card design that encompasses a clean cut, modern style with a retro flare. website is bramblewoodcardco.com for reference. Can utilize a comic book era feel or a more modern outdoor feel to utilize the "Pacific Northwest" elements of tress, mountains, etc.

Industry/Entity Type

Trading cards and collectibles

Contact Information for Business Card

business name, email address, phone number, name, owner job title

Font styles to use
Sans Serif

```html
<!DOCTYPE html>
<html lang="en">
<head>
<meta charset="utf-8">
<title>Bramblewood Card Company – Business Cards</title>
<link href="https://fonts.googleapis.com/css2?family=Montserrat:wght@700;800&family=Josefin+Sans:wght@400;600&display=swap" rel="stylesheet">
<style>
  :root {
    --backdrop: #4a2e1f;
    --sky: #20bfe0;
    --slate: #757575;
    --paper: #ffffff;
  }
  * { box-sizing: border-box; margin: 0; padding: 0; }
  html, body {
    width: 1200px; height: 1200px; overflow: hidden;
    background: var(--backdrop);
  }
  .canvas { position: relative; width: 1200px; height: 1200px; }

  .card {
    position: absolute; top: 222px;
    width: 454px; height: 756px;
  }
  .card--front { left: 117px; background: var(--slate); }
  .card--back  { left: 639px; background: var(--paper); }

  .panel {
    position: absolute; left: 37px; top: 34px;
    width: 383px; height: 685px;
    background: var(--sky);
    border-radius: 12px;
    overflow: hidden;
  }
  .card--front .panel { border: 8px solid var(--paper); }
  .card--back .panel  { border: 8px solid var(--slate); }

  .brand-mark {
    position: absolute; left: 0; right: 0;
    display: flex; flex-direction: column; align-items: center;
    font-family: "Montserrat", sans-serif; font-weight: 700;
    color: var(--slate); text-align: center; text-transform: uppercase;
  }
  .brand-mark__dot {
    width: 54px; height: 54px; border-radius: 50%;
    background: var(--slate); margin-bottom: 14px;
  }
  .card--front .brand-mark { top: 48px; font-size: 18px; letter-spacing: 2px; line-height: 1.3; }
  .card--back .brand-mark { top: 150px; font-size: 30px; letter-spacing: 2px; line-height: 1.25; }
  .card--back .brand-mark__dot { width: 90px; height: 90px; margin-bottom: 22px; }

  .company-name {
    position: absolute; left: 0; right: 0; top: 254px;
    font-family: "Montserrat", sans-serif; font-weight: 800;
    font-size: 34px; line-height: 40px;
    color: var(--paper); text-align: center; text-transform: uppercase;
  }

  .person-name {
    position: absolute; left: 0; right: 0; top: 385px;
    font-family: "Josefin Sans", sans-serif; font-size: 31px;
    color: var(--paper); text-align: center;
  }

  .job-ribbon { position: absolute; left: 94px; top: 425px; width: 180px; height: 42px; }
  .job-ribbon__label {
    position: absolute; left: 0; right: 0; top: 9px;
    font-family: "Josefin Sans", sans-serif; font-size: 22px;
    color: var(--paper); text-align: center;
  }

  .contact-rule { position: absolute; left: 72px; width: 222px; height: 30px; }
  .contact-rule--phone { top: 486px; }
  .contact-rule--mail  { top: 573px; }

  .contact-text {
    position: absolute; left: 0; right: 0;
    font-family: "Josefin Sans", sans-serif; font-size: 22px;
    color: var(--paper); text-align: center; letter-spacing: 0.5px;
  }
  .contact-text--phone { top: 524px; }
  .contact-text--mail  { top: 610px; font-size: 21px; }

  .ridge-band {
    position: absolute; left: 0; right: 0; bottom: 0; height: 120px;
    background: linear-gradient(to bottom, rgba(117,117,117,0) 0%, var(--slate) 55%);
  }
</style>
</head>
<body>
<main class="canvas">

  <section class="card card--front" aria-label="Business card front">
    <div class="panel">
      <div class="brand-mark">
        <span class="brand-mark__dot"></span>
        <span>Bramblewood</span>
        <span>Card Company</span>
      </div>

      <h1 class="company-name">Bramblewood<br>Card Company</h1>

      <p class="person-name">Your Name</p>

      <div class="job-ribbon">
        <svg width="180" height="42" viewBox="0 0 180 42" aria-hidden="true">
          <polygon points="0,6 28,6 28,40 12,40 18,23" fill="var(--slate)"/>
          <polygon points="180,6 152,6 152,40 168,40 162,23" fill="var(--slate)"/>
          <rect x="21" y="0" width="138" height="36" fill="var(--slate)"/>
          <rect x="21" y="0" width="138" height="36" fill="none" stroke="var(--sky)" stroke-width="2"/>
        </svg>
        <span class="job-ribbon__label">Job Title</span>
      </div>

      <svg class="contact-rule contact-rule--phone" viewBox="0 0 222 30" aria-hidden="true">
        <g stroke="var(--paper)" stroke-width="2.5">
          <line x1="0" y1="12" x2="88" y2="12"/><line x1="0" y1="18" x2="88" y2="18"/>
          <line x1="134" y1="12" x2="222" y2="12"/><line x1="134" y1="18" x2="222" y2="18"/>
        </g>
        <polygon points="111,0 124,7.5 124,22.5 111,30 98,22.5 98,7.5" fill="var(--slate)"/>
        <path d="M106 8 l3 0 l1.5 4 l-2 1.5 q1.5 3.5 5 5 l1.5 -2 l4 1.5 l0 3 q-1 1.5 -3 1.5 q-10 -1 -11 -11 q0 -2 1 -3.5z" fill="var(--paper)"/>
      </svg>
      <p class="contact-text contact-text--phone">123 123 123</p>

      <svg class="contact-rule contact-rule--mail" viewBox="0 0 222 30" aria-hidden="true">
        <g stroke="var(--paper)" stroke-width="2.5">
          <line x1="0" y1="12" x2="88" y2="12"/><line x1="0" y1="18" x2="88" y2="18"/>
          <line x1="134" y1="12" x2="222" y2="12"/><line x1="134" y1="18" x2="222" y2="18"/>
        </g>
        <polygon points="111,0 124,7.5 124,22.5 111,30 98,22.5 98,7.5" fill="var(--slate)"/>
        <rect x="103" y="10" width="16" height="11" rx="1.5" fill="var(--paper)"/>
        <polyline points="103.5,11 111,17 118.5,11" fill="none" stroke="var(--slate)" stroke-width="1.5"/>
      </svg>
      <p class="contact-text contact-text--mail">name@email.com</p>
    </div>
  </section>

  <section class="card card--back" aria-label="Business card back">
    <div class="panel">
      <div class="brand-mark">
        <span class="brand-mark__dot"></span>
        <span>Bramblewood</span>
        <span>Card Company</span>
      </div>
      <div class="ridge-band" role="img" aria-label="Mountain range silhouette along the bottom edge"></div>
    </div>
  </section>

</main>
</body>
</html>
```